Maple Roster Business Card for recruitment company

We are looking for a Business Card Design that incorporates our personal details and our busines name and logo. We are a specialized search consultancy that recruit Property and Construction professionals.
We would like a business card that stands out and is appealing to the Construction and Property industry as well.

Target Market(s)

people in the construction and property industry

Contact Information for Business Card

Business Name and logo

Font styles to use
Serif

Colors
0094D4
00A9DD
6FCCEA
C7EBF8
E9F6FB

Requirements
Must have
• Business name and logo as well as contact details
Should not have
• No photos of us please

```html
<!DOCTYPE html>
<html lang="en">
<head>
<meta charset="utf-8">
<title>Maple Roster Business Card</title>
<link href="https://fonts.googleapis.com/css2?family=Roboto:wght@300;400&display=swap" rel="stylesheet">
<style>
  :root {
    --backdrop: #9a9b9a;
    --card-light: #ffffff;
    --card-dark: #262729;
    --ink-navy: #0f3a50;
    --ink-grey: #6f6f6f;
    --brand-blue: #1e93d8;
  }
  * { margin: 0; padding: 0; box-sizing: border-box; }
  html, body { width: 1200px; height: 1200px; overflow: hidden; }
  body {
    background: var(--backdrop);
    font-family: "Roboto", Arial, sans-serif;
    position: relative;
  }
  .card {
    position: absolute;
    left: 222px;
    width: 755px;
    height: 462px;
  }
  .card--front { top: 105px; background: var(--card-light); }
  .card--back { top: 630px; background: var(--card-dark); }

  .wordmark {
    position: absolute;
    font-weight: 300;
    text-transform: uppercase;
    white-space: nowrap;
    line-height: 1;
  }
  .card--front .wordmark {
    left: 44px; top: 67px;
    font-size: 56px;
    color: var(--ink-navy);
    letter-spacing: 1px;
  }
  .card--back .wordmark {
    left: 0; right: 0; top: 192px;
    text-align: center;
    font-size: 92px;
    color: var(--brand-blue);
    letter-spacing: 2px;
  }

  .person {
    position: absolute;
    right: 43px; top: 194px;
    text-align: right;
  }
  .person__name { font-size: 37px; font-weight: 400; color: var(--ink-navy); line-height: 44px; }
  .person__role { font-size: 25px; font-weight: 400; color: var(--ink-grey); line-height: 30px; }

  .divider {
    position: absolute;
    left: 44px; right: 43px; top: 283px;
    height: 3px;
    background: var(--ink-navy);
  }

  .contacts {
    position: absolute;
    left: 44px; top: 303px;
    list-style: none;
  }
  .contacts li {
    display: flex;
    align-items: center;
    height: 29.5px;
    font-size: 22px;
    font-weight: 300;
    color: var(--ink-grey);
  }
  .contacts svg { width: 20px; height: 20px; margin-right: 16px; fill: var(--ink-navy); }

  .address {
    position: absolute;
    right: 43px; top: 344px;
    text-align: right;
    font-size: 22px;
    font-weight: 300;
    color: var(--ink-grey);
    line-height: 27px;
  }
  .address svg { width: 18px; height: 26px; fill: var(--ink-navy); display: block; margin: 0 0 4px auto; }
</style>
</head>
<body>
  <section class="card card--front">
    <div class="wordmark">Maple Roster</div>

    <div class="person">
      <div class="person__name">Dana Whitfield</div>
      <div class="person__role">President</div>
    </div>

    <div class="divider"></div>

    <ul class="contacts">
      <li>
        <svg viewBox="0 0 24 24" aria-hidden="true"><path d="M6.6 10.8a15.1 15.1 0 0 0 6.6 6.6l2.2-2.2a1 1 0 0 1 1-.25 11.4 11.4 0 0 0 3.6.57 1 1 0 0 1 1 1V20a1 1 0 0 1-1 1A17 17 0 0 1 3 4a1 1 0 0 1 1-1h3.5a1 1 0 0 1 1 1c0 1.25.2 2.45.57 3.57a1 1 0 0 1-.25 1z"/></svg>
        021 5550 1234
      </li>
      <li>
        <svg viewBox="0 0 24 24" aria-hidden="true"><path d="M7 2h10v5H7zM4 8h16a2 2 0 0 1 2 2v7h-4v5H6v-5H2v-7a2 2 0 0 1 2-2zm4 8v4h8v-4z"/></svg>
        02155501299
      </li>
      <li>
        <svg viewBox="0 0 24 24" aria-hidden="true"><path d="M2 4h20v9a6 6 0 0 0-9 7H2zm2 2v.4l8 5.2 8-5.2V6H4z"/><circle cx="18.5" cy="18.5" r="4.5"/><path d="M16.5 18.5l1.5 1.5 2.5-2.8" stroke="#fff" stroke-width="1.4" fill="none"/></svg>
        info@mapleroster.com
      </li>
      <li>
        <svg viewBox="0 0 24 24" aria-hidden="true"><path d="M12 2a10 10 0 1 0 0 20 10 10 0 0 0 0-20zm0 1.6c1.2 1.3 2.1 3.2 2.4 5.4H9.6c.3-2.2 1.2-4.1 2.4-5.4zM8 9H3.9a8.4 8.4 0 0 1 5.4-5C8.6 5.5 8.1 7.2 8 9zm0 1.6c0 1 .1 1.9.3 2.8H3.8a8.4 8.4 0 0 1 0-2.8zm1.6 0h4.8a14 14 0 0 1-.2 2.8H9.8a14 14 0 0 1-.2-2.8zm6.4 0h4.2a8.4 8.4 0 0 1 0 2.8h-4.5c.2-.9.3-1.8.3-2.8zm0-1.6c-.1-1.8-.6-3.5-1.3-5a8.4 8.4 0 0 1 5.4 5zM4.3 15h4.4c.3 1.9 1 3.6 1.8 4.9A8.4 8.4 0 0 1 4.3 15zm6 0h3.4c-.3 1.7-1 3.3-1.7 4.4-.7-1.1-1.4-2.7-1.7-4.4zm5 0h4.4a8.4 8.4 0 0 1-6.2 4.9c.8-1.3 1.5-3 1.8-4.9z"/></svg>
        www.mapleroster.com
      </li>
    </ul>

    <div class="address">
      <svg viewBox="0 0 18 26" aria-hidden="true"><path d="M9 0a9 9 0 0 0-9 9c0 6.8 9 17 9 17s9-10.2 9-17a9 9 0 0 0-9-9zm0 12.5A3.5 3.5 0 1 1 9 5.5a3.5 3.5 0 0 1 0 7z"/></svg>
      48 Harbor Lane Suite 200<br>
      Westfield 5551
    </div>
  </section>

  <section class="card card--back">
    <div class="wordmark">Maple Roster</div>
  </section>
</body>
</html>
```